Business Card Design for Marketing Firm

Looking for business card design for higher end marketing firm. Clean but impressionable/trendy. We are a marketing firm that represents manufacturers in the foodservice equipment and supply industry. Our customers are end users such has hotels, restaurants, country clubs, convention centers and casinos as well as distributors of restaurants supplies and equipment, and manufacturers of foodservice equipment and supplies.
Target Market(s)
Hotels, Restaurants, Supply & Equipment Distributors, Foodservice Manufacturers
Industry/Entity Type
Foodservice/Hospitality
Contact Information for Business Card
Name, Title, Contact Number, Email, Website, Social Media, Address
Requirements
Must have
- Clean & Simple but Serious and Impressionable

```html
<!DOCTYPE html>
<html lang="en">
<head>
<meta charset="utf-8">
<title>Meridian Service Reps – Business Card</title>
<link rel="stylesheet" href="https://fonts.googleapis.com/css2?family=Arimo:wght@400;700&display=swap">
<style>
  :root {
    --stage: #141416;
    --card-navy: #07077c;
    --card-navy-deep: #050566;
    --ink-white: #ffffff;
    --ink-soft: rgba(255,255,255,0.88);
    --rule: rgba(255,255,255,0.8);
  }
  * { box-sizing: border-box; margin: 0; padding: 0; }
  html, body {
    width: 1200px; height: 963px; overflow: hidden;
    background: var(--stage);
    font-family: "Arimo", Arial, sans-serif;
    color: var(--ink-white);
  }
  .stage {
    position: relative; width: 1200px; height: 963px;
    display: flex; flex-direction: column; align-items: center; justify-content: center; gap: 70px;
  }
  .card {
    position: relative; width: 520px; height: 297px; border-radius: 16px;
    background: linear-gradient(135deg, var(--card-navy) 0%, var(--card-navy-deep) 100%);
    overflow: hidden;
  }

  /* Front side */
  .card-front .brand {
    position: absolute; left: 50%; top: 50%; transform: translate(-50%, -50%);
    text-align: right; text-transform: uppercase; font-weight: 400;
  }
  .card-front .brand-main { font-size: 30px; letter-spacing: 2px; line-height: 1.1; white-space: nowrap; }
  .card-front .brand-sub { font-size: 20px; letter-spacing: 2px; line-height: 1.2; }

  /* Back side */
  .card-back .brand {
    position: absolute; top: 52px; left: 50%; transform: translateX(-42%);
    display: flex; align-items: center; gap: 12px;
    text-transform: uppercase; font-weight: 400;
  }
  .brand-dot { width: 12px; height: 12px; border-radius: 50%; background: var(--ink-white); flex: none; }
  .card-back .brand-text { text-align: right; }
  .card-back .brand-main { font-size: 20px; letter-spacing: 1.5px; line-height: 1.1; white-space: nowrap; }
  .card-back .brand-sub { font-size: 14px; letter-spacing: 1.5px; }

  .person {
    position: absolute; top: 150px; right: 280px; text-align: right;
  }
  .person-name { font-size: 17px; font-weight: 700; letter-spacing: 0.5px; text-transform: uppercase; }
  .person-title { font-size: 13px; color: var(--ink-soft); margin-top: 3px; }

  .divider { position: absolute; left: 258px; top: 146px; width: 1px; height: 62px; background: var(--rule); }

  .contact-list { position: absolute; left: 274px; top: 146px; list-style: none; }
  .contact-item { display: flex; align-items: center; gap: 8px; font-size: 13.5px; line-height: 21px; }
  .contact-item svg { width: 12px; height: 12px; flex: none; }

  .address { position: absolute; left: 62px; top: 228px; font-size: 13.5px; color: var(--ink-soft); }
</style>
</head>
<body>
<main class="stage">
  <section class="card card-front" aria-label="Card front">
    <div class="brand">
      <div class="brand-main">Meridian Service</div>
      <div class="brand-sub">Reps</div>
    </div>
  </section>

  <section class="card card-back" aria-label="Card back">
    <div class="brand">
      <span class="brand-dot"></span>
      <div class="brand-text">
        <div class="brand-main">Meridian Service</div>
        <div class="brand-sub">Reps</div>
      </div>
    </div>

    <div class="person">
      <div class="person-name">Daniel Reed</div>
      <div class="person-title">Manager</div>
    </div>

    <span class="divider"></span>

    <ul class="contact-list">
      <li class="contact-item">
        <svg viewBox="0 0 24 24" fill="none" stroke="#fff" stroke-width="2.2" stroke-linecap="round" stroke-linejoin="round"><path d="M5 3h4l2 5-3 2a12 12 0 0 0 6 6l2-3 5 2v4a2 2 0 0 1-2 2A18 18 0 0 1 3 5a2 2 0 0 1 2-2z"/></svg>
        <span>123-456-2100</span>
      </li>
      <li class="contact-item">
        <svg viewBox="0 0 24 24" fill="none" stroke="#fff" stroke-width="2.2" stroke-linejoin="round"><rect x="2" y="5" width="20" height="14" rx="2"/><path d="M2 6l10 7 10-7"/></svg>
        <span>youremail@example.com</span>
      </li>
      <li class="contact-item">
        <svg viewBox="0 0 24 24" fill="none" stroke="#fff" stroke-width="2"><circle cx="12" cy="12" r="10"/><path d="M2 12h20M12 2c3 3 4 6.5 4 10s-1 7-4 10c-3-3-4-6.5-4-10s1-7 4-10z"/></svg>
        <span>www.yourwebsite.com</span>
      </li>
    </ul>

    <p class="address">Your Address, City, State, Zip 0000</p>
  </section>
</main>
</body>
</html>
```